Hollow Mesa Farm Vault Reserve Wine Label (Front and Back)

I need to create an elite tier wine label.  I would like it to be in a light, natural color with silver or gold.  I would like it to look rich and expensive, mostly monochromatic, elegantly simple.  It will need to stand up next to wine labels that are black and charcoal colored and look like the more expensive wine of the 3.  I have attached a similar label that it will be grouped with and some instructions.
We are a winery in southeast Washington state with a reputation for fine wines and top notch terroir.  We want to present family, tradition and high value wine in the bottle.

```html
<!DOCTYPE html>
<html lang="en">
<head>
<meta charset="utf-8">
<title>Hollow Mesa Farm – Vault Reserve Label</title>
<link rel="stylesheet" href="https://fonts.googleapis.com/css2?family=Cinzel:wght@400;600;700&family=Lora:wght@400;500&family=Allison&display=swap">
<style>
  :root {
    --backdrop: #e8e8e8;
    --paper-light: #f4f4f5;
    --paper-mid: #e6e6e8;
    --ink: #2b2b2e;
    --ink-soft: #3c3c40;
    --silver: #c9c9cc;
    --silver-light: #e2e2e4;
    --gold: #c58a2f;
    --gold-light: #e6c77c;
    --gold-deep: #b77a22;
  }
  html, body {
    margin: 0;
    padding: 0;
    width: 1110px;
    height: 1200px;
    overflow: hidden;
    background: var(--backdrop);
  }
  .canvas {
    position: relative;
    width: 1110px;
    height: 1200px;
  }
  .label {
    position: absolute;
    left: 202px;
    top: 50px;
    width: 706px;
    height: 1100px;
    background: radial-gradient(ellipse at 50% 40%, var(--paper-light) 0%, var(--paper-mid) 100%);
    box-shadow: 0 1px 3px rgba(0,0,0,0.12);
    text-align: center;
    color: var(--ink);
  }
  .label > * {
    position: absolute;
    left: 0;
    right: 0;
    margin: 0;
  }
  .winery-name {
    top: 102px;
    font-family: "Cinzel", serif;
    font-weight: 400;
    font-size: 64px;
    line-height: 98px;
    letter-spacing: 1px;
    color: var(--ink);
  }
  .appellation {
    top: 344px;
    font-family: "Cinzel", serif;
    font-weight: 600;
    font-size: 29px;
    letter-spacing: 7px;
    color: var(--ink-soft);
  }
  .crest {
    top: 440px;
    height: 195px;
  }
  .crest-wing {
    position: absolute;
    top: 54px;
    width: 215px;
    height: 96px;
    background: linear-gradient(90deg, rgba(201,201,204,0) 0%, var(--silver-light) 35%, var(--silver) 100%);
    opacity: 0.85;
  }
  .crest-wing--left { left: 48px; }
  .crest-wing--right {
    right: 48px;
    transform: scaleX(-1);
  }
  .crest-mark {
    position: absolute;
    left: 50%;
    top: 0;
    transform: translateX(-50%);
    width: 176px;
    height: 195px;
    display: flex;
    align-items: center;
    justify-content: center;
    gap: 10px;
  }
  .crest-square {
    width: 14px;
    height: 14px;
    background: var(--gold);
    flex: none;
  }
  .crest-name {
    font-family: "Cinzel", serif;
    font-weight: 600;
    font-size: 28px;
    line-height: 38px;
    letter-spacing: 2px;
    color: var(--gold);
    text-align: left;
  }
  .vineyard {
    top: 700px;
    font-family: "Lora", serif;
    font-weight: 400;
    font-size: 30px;
    letter-spacing: 1.5px;
    color: var(--ink);
  }
  .tier {
    top: 766px;
    font-family: "Cinzel", serif;
    font-weight: 700;
    font-size: 58px;
    letter-spacing: 1px;
    color: var(--ink-soft);
    text-shadow: -2px 2px 0 var(--gold-light);
  }
  .varietal {
    top: 852px;
    font-family: "Allison", cursive;
    font-size: 76px;
    line-height: 90px;
    color: var(--gold);
  }
  .vintage {
    top: 958px;
    font-family: "Lora", serif;
    font-size: 30px;
    color: var(--ink);
  }
  .heritage-band {
    top: 1032px;
    height: 64px;
    background: linear-gradient(90deg, var(--gold-deep) 0%, var(--gold-light) 30%, #d9b061 60%, var(--gold-light) 85%, var(--gold-deep) 100%);
    display: flex;
    align-items: center;
    justify-content: center;
    font-family: "Lora", serif;
    font-size: 21px;
    letter-spacing: 0.5px;
    color: var(--ink-soft);
  }
</style>
</head>
<body>
  <main class="canvas">
    <article class="label">
      <h1 class="winery-name">HOLLOW MESA<br>FARM</h1>
      <p class="appellation">HORSE HEAVEN HILLS</p>

      <div class="crest">
        <div class="crest-wing crest-wing--left" role="img" aria-label="Silver ornamental flourish"></div>
        <div class="crest-mark">
          <span class="crest-square"></span>
          <span class="crest-name">HOLLOW<br>MESA<br>FARM</span>
        </div>
        <div class="crest-wing crest-wing--right" role="img" aria-label="Silver ornamental flourish"></div>
      </div>

      <p class="vineyard">ESTATE VINEYARD</p>
      <h2 class="tier">VAULT RESERVE</h2>
      <p class="varietal">Cabernet Sauvignon</p>
      <p class="vintage">2022</p>
      <p class="heritage-band">FAMILY STEWARDS OF THE LAND FOR 5 GENERATIONS</p>
    </article>
  </main>
</body>
</html>
```